New Business Card Design

We would like to refresh our business cards and make them look better. We are an IT company specialising in Cloud Services, IT Managed Services, software and hardware. I have attached a PSD of our current design. Also attached our logo.
Updates

I have uploaded all new logos in EPS format.

Can you please edit all designs to include a job title for Marcus Hollis, eg. General Manager

Industry/Entity Type

Software

Colors
ffffff

Requirements
Must have
• Please use white background.
Should not have
• Black background

```html
<!DOCTYPE html>
<html lang="en">
<head>
<meta charset="utf-8">
<title>Clarion Technology – Business Card</title>
<link rel="stylesheet" href="https://fonts.googleapis.com/css2?family=Open+Sans:wght@400;600;700&display=swap">
<style>
  :root{
    --page:#e9eaee;
    --card:#ffffff;
    --brand-red:#c0392b;
    --slate:#848e98;
    --ink:#2b2f33;
    --ink-soft:#3d4247;
  }
  *{box-sizing:border-box;margin:0;padding:0}
  html,body{width:1200px;height:987px;overflow:hidden}
  body{
    background:var(--page);
    font-family:"Open Sans",Arial,sans-serif;
    display:flex;align-items:center;justify-content:center;gap:40px;
  }
  .card{
    position:relative;width:540px;height:309px;
    background:var(--card);border-radius:18px;overflow:hidden;
    box-shadow:0 6px 18px rgba(0,0,0,.12);
  }
  .card-art{position:absolute;inset:0;width:100%;height:100%}
  .brand{display:flex;align-items:center;gap:12px}
  .brand-dot{width:34px;height:34px;border-radius:50%;background:var(--brand-red);flex:none}
  .brand-name{font-size:26px;font-weight:400;color:var(--ink);letter-spacing:2px;line-height:1}

  /* front */
  .front .brand{position:absolute;left:30px;top:36px}
  .holder{position:absolute;left:30px;top:84px}
  .holder-name{font-size:17px;font-weight:700;color:var(--brand-red);line-height:1.2}
  .holder-title{font-size:12px;color:var(--ink);line-height:1.4}
  .contacts{position:absolute;right:28px;top:206px;list-style:none;text-align:right}
  .contacts li{display:flex;align-items:center;justify-content:flex-end;gap:8px;
    color:#fff;font-size:13px;line-height:22px}
  .contacts svg{width:13px;height:13px;fill:#fff;flex:none}

  /* back */
  .back{display:flex;flex-direction:column;align-items:center;justify-content:center;text-align:center}
  .back .brand{margin-bottom:26px}
  .tagline{font-size:15px;color:var(--ink-soft);line-height:1.45}
  .web{margin-top:18px;font-size:12px;letter-spacing:3px;color:var(--ink-soft)}
  .web strong{color:var(--brand-red);font-weight:600}
</style>
</head>
<body>
  <section class="card front" aria-label="Card front">
    <svg class="card-art" viewBox="0 0 540 309" preserveAspectRatio="none" aria-hidden="true">
      <path d="M0,160 C150,215 330,222 540,190 L540,309 L0,309 Z" fill="var(--slate)"/>
      <path d="M0,124 C120,200 320,216 540,182 C320,208 140,204 0,146 Z" fill="var(--brand-red)"/>
    </svg>
    <div class="brand">
      <span class="brand-dot"></span>
      <span class="brand-name">Clarion Technology</span>
    </div>
    <div class="holder">
      <p class="holder-name">Marcus Hollis</p>
      <p class="holder-title">General Manager</p>
    </div>
    <ul class="contacts">
      <li><svg viewBox="0 0 24 24"><path d="M6.6 10.8a15.1 15.1 0 0 0 6.6 6.6l2.2-2.2c.3-.3.7-.4 1-.2 1.1.4 2.3.6 3.6.6.6 0 1 .4 1 1V20c0 .6-.4 1-1 1A17 17 0 0 1 3 4c0-.6.4-1 1-1h3.5c.6 0 1 .4 1 1 0 1.3.2 2.5.6 3.6.1.3 0 .7-.2 1z"/></svg>07 3555 0148</li>
      <li><svg viewBox="0 0 24 24"><path d="M7 1h10a2 2 0 0 1 2 2v18a2 2 0 0 1-2 2H7a2 2 0 0 1-2-2V3a2 2 0 0 1 2-2zm0 3v14h10V4zm5 15.5a1 1 0 1 0 0 2 1 1 0 0 0 0-2z"/></svg>0400 555 217</li>
      <li><svg viewBox="0 0 24 24"><path d="M2 5h20v14H2zm2 2v.4l8 5 8-5V7zm0 2.8V17h16V9.8l-8 5z"/></svg>mhollis@clarionit.com.au</li>
      <li><svg viewBox="0 0 24 24"><path d="M12 2a10 10 0 1 0 0 20 10 10 0 0 0 0-20zm6.9 9h-3a15 15 0 0 0-1.3-5.6A8 8 0 0 1 18.9 11zM12 4c.9 1.2 1.8 3.6 1.9 7h-3.8c.1-3.4 1-5.8 1.9-7zM9.4 5.4A15 15 0 0 0 8.1 11h-3a8 8 0 0 1 4.3-5.6zM5.1 13h3a15 15 0 0 0 1.3 5.6A8 8 0 0 1 5.1 13zm6.9 7c-.9-1.2-1.8-3.6-1.9-7h3.8c-.1 3.4-1 5.8-1.9 7zm2.6-1.4a15 15 0 0 0 1.3-5.6h3a8 8 0 0 1-4.3 5.6z"/></svg>www.clarionit.com.au</li>
    </ul>
  </section>

  <section class="card back" aria-label="Card back">
    <div class="brand">
      <span class="brand-dot"></span>
      <span class="brand-name">Clarion Technology</span>
    </div>
    <p class="tagline">We are an IT company specializing in Cloud Services<br>IT Managed Services, software and hardware</p>
    <p class="web">www.<strong>clarionit</strong>.com.au</p>
  </section>
</body>
</html>
```